Information One Page for Email

I am looking for a informative attachment I can send with an introductive email for Meridale Slab Works. Something I can also Mail.

Meridale Slab Works is the leader in Rebar Post Tension Cable Placement and Post Tension Cable repair. Outside of cable placement and repair we do concrete repair, Parking Garage restoration and
Updates

Content

Post Tension Repair and Concrete Restoration
Post-tensioning is a revolutionary method in concrete construction that enhances the strength and durability of structures. However, like all construction ele-ments, post-tension cables can experience wear and damage over time. Ensuring timely and effective repair is crucial for maintaining the safety and integrity of your building.
Why Post-Tension Cable Repair is Essential
1. **Structural Integrity**: Damaged or deteriorated cables can compromise the structural integrity of your building, leading to safety hazards and potential structural failures.
2. **Extended Lifespan**: Regular maintenance and repair of post-tension cables extend the lifespan of your structure, ensuring it remains safe and function-al for years to come.
3. **Cost-Effective**: Addressing cable issues early on prevents more severe damage and costly repairs down the line.
Common Signs of Post-Tension Cable Issues
- Cracks in concrete surfaces
- Unusual noises or popping sounds
- Visible cable ends or broken strands
- Water leakage through cracks
Our Repair Process
1. **Inspection and Assessment**: Our team conducts a thorough inspection to identify the extent of the damage and determine the appropriate repair meth-ods.
2. **Cable Repair or Replacement**: Depending on the severity, we either re-pair the existing cables or replace them with new ones to restore full functional-ity.
3. **Sealing and Protection**: After repairing, we seal the affected areas to protect against moisture and future damage.
4. **Quality Assurance**: We perform rigorous quality checks to ensure the repairs meet industry standards and the structure is safe for use.
Why Choose Us
- **Expertise and Experience**: With years of experience in post-tension cable repair, our team is skilled in handling even the most complex repairs efficiently and effectively.
- **Advanced Technology**: We use the latest technology and materials to ensure durable and long-lasting repairs.
- **Customer Satisfaction**: Our commitment to quality and customer satisfaction sets us apart. We work closely with our clients to ensure their needs are met and expectations exceeded.
Contact Us
If you suspect issues with your post-tension cables or need a routine inspection, don't hesitate to contact us. Our experts are ready to provide the best solutions to keep your structures safe and secure.
Ensure the safety and longevity of your building with our professional post-tension cable repair services. Trust us to deliver quality and reliability every time.

```html
<!DOCTYPE html>
<html lang="en">
<head>
<meta charset="utf-8">
<title>Meridale Slab Works LLC – Post-Tension Repair &amp; Concrete Restoration</title>
<link rel="stylesheet" href="https://fonts.googleapis.com/css2?family=Open+Sans:ital,wght@0,400;0,600;0,700;0,800;1,400;1,600&display=swap">
<style>
  :root {
    --green: #1d5a3c;
    --green-dark: #134a30;
    --green-deep: #1f4a3b;
    --paper: #e4e5e5;
    --paper-light: #eeefef;
    --paper-shade: #d6d8d8;
    --ink: #2b2f2e;
    --rule: #9fa4a3;
    --white: #ffffff;
    --backdrop: #eceeed;
  }
  * { box-sizing: border-box; margin: 0; padding: 0; }
  html, body { width: 900px; height: 1200px; overflow: hidden; }
  body {
    background: var(--backdrop);
    font-family: "Open Sans", Arial, sans-serif;
    color: var(--ink);
    position: relative;
  }
  .flyer {
    position: absolute; left: 50px; top: 0;
    width: 800px; height: 1200px;
    background: linear-gradient(180deg, var(--paper-light) 0%, var(--paper) 55%, var(--paper-shade) 100%);
    overflow: hidden;
  }
  .abs { position: absolute; }

  /* Header */
  .hero-photo {
    position: absolute; left: 0; top: 0; width: 800px; height: 300px;
    background: linear-gradient(180deg, #d9dcdf 0%, #c9cdd1 45%, #a9aeae 80%, #c7c9c8 100%);
  }
  .hero-building {
    position: absolute; right: 0; top: 70px; width: 190px; height: 200px;
    background: linear-gradient(180deg, #9b9e9f, #7d8182);
  }
  .hero-waves { position: absolute; left: 0; top: 170px; }
  .brand {
    position: absolute; left: 36px; top: 48px;
    display: flex; align-items: center; gap: 14px;
  }
  .brand-mark { width: 22px; height: 22px; background: var(--green); }
  .brand-name {
    font-weight: 800; color: var(--green); font-size: 40px; line-height: 1.05;
  }

  /* Section headings */
  .tab {
    position: absolute; left: 0; height: 26px;
    background: var(--green);
    color: var(--white); font-weight: 700; font-size: 16.5px; letter-spacing: .2px;
    padding-left: 50px; line-height: 26px;
    clip-path: polygon(0 0, 100% 0, calc(100% - 12px) 100%, 0 100%);
  }
  .tab-rule { position: absolute; height: 1px; background: var(--rule); }

  .who-title { left: 52px; top: 280px; font-size: 17px; font-weight: 700; color: var(--green-dark); }
  .who-rule { left: 52px; top: 306px; width: 395px; }
  .who-text { left: 52px; top: 316px; width: 700px; font-size: 15px; line-height: 26px; color: #3a3f3e; }
  .who-text strong { color: var(--green-dark); font-weight: 700; }

  .services-band {
    position: absolute; left: 0; top: 411px; width: 800px; height: 100px;
    background: linear-gradient(180deg, #d7d9d9, #cfd2d2);
  }
  .services { position: absolute; left: 44px; top: 449px; width: 730px; display: flex; }
  .service {
    display: flex; align-items: center; gap: 8px;
    font-size: 14px; line-height: 20px; color: #2c3231;
    padding: 0 10px; border-right: 1px solid var(--rule);
  }
  .service:last-child { border-right: 0; }
  .service svg { flex: none; }

  /* Feature panel */
  .panel {
    position: absolute; left: 41px; top: 524px; width: 718px; height: 173px;
    background: #d9dbdb;
  }
  .panel-title {
    position: absolute; left: 0; top: 0; width: 718px; height: 34px;
    background: var(--green); color: var(--white);
    font-weight: 700; font-size: 17px; text-align: center; line-height: 34px;
    clip-path: polygon(0 0, 100% 0, calc(100% - 10px) 100%, 0 100%);
  }
  .panel-tagline {
    position: absolute; left: 0; top: 42px; width: 718px; text-align: center;
    font-style: italic; font-weight: 600; font-size: 12.5px; color: #333;
  }
  .panel-tagline::before, .panel-tagline::after {
    content: ""; display: inline-block; width: 112px; height: 1px; background: var(--rule);
    vertical-align: middle; margin: 0 8px;
  }
  .benefits { position: absolute; left: 0; top: 73px; width: 718px; display: flex; }
  .benefit { text-align: center; border-right: 1px solid var(--rule); }
  .benefit:last-child { border-right: 0; }
  .benefit h3 {
    background: var(--green); color: var(--white); font-size: 16.5px; font-weight: 700;
    height: 38px; line-height: 38px;
  }
  .benefit p { font-size: 13.5px; line-height: 19px; padding: 10px 24px 12px; color: #2f3433; }

  /* Warning signs */
  .signs { position: absolute; left: 38px; top: 755px; display: flex; gap: 8px; }
  .sign { background: #d3d5d5; }
  .sign-photo { height: 58px; }
  .sign-label {
    display: flex; align-items: center; justify-content: center; gap: 7px;
    height: 32px; font-size: 14px; font-weight: 600; color: #222;
  }

  /* Process */
  .process { position: absolute; left: 46px; top: 895px; font-size: 14.5px; color: #2b302f; }
  .step {
    position: absolute; display: flex; align-items: center; gap: 10px;
    white-space: nowrap; padding-bottom: 4px; border-bottom: 1px solid var(--rule);
  }
  .col-rule { position: absolute; width: 1px; background: var(--rule); }

  /* Why choose us */
  .why { position: absolute; left: 46px; top: 1016px; width: 280px; }
  .why li {
    list-style: none; display: flex; align-items: center; gap: 10px;
    font-size: 14.5px; color: #222; height: 32px; border-bottom: 1px solid var(--rule);
  }
  .tick-box { width: 16px; height: 16px; background: var(--green); display: grid; place-items: center; flex: none; }

  .footer-band { position: absolute; left: 0; top: 1135px; width: 800px; height: 65px; background: #c9cccc; }
  .updated { left: 46px; top: 1145px; font-size: 12px; font-style: italic; color: #333; }

  /* Contact */
  .contact {
    position: absolute; left: 318px; top: 987px; width: 482px; height: 213px;
    background: linear-gradient(160deg, #245a40, var(--green-dark));
    clip-path: polygon(70px 0, 100% 0, 100% 100%, 0 100%);
    color: var(--white);
  }
  .contact h2 { position: absolute; left: 90px; top: 12px; font-size: 20px; font-weight: 700; }
  .contact-head-rule { position: absolute; left: 248px; top: 28px; width: 234px; height: 1px; background: rgba(255,255,255,.5); }
  .contact-line {
    position: absolute; left: 90px; width: 350px; display: flex; align-items: center; gap: 12px;
    border-bottom: 1px solid rgba(255,255,255,.35); padding-bottom: 6px;
  }
  .contact-phone { top: 48px; font-size: 20px; font-weight: 700; }
  .contact-email { top: 82px; font-size: 14px; }
  .contact-web { top: 116px; font-size: 14px; }
</style>
</head>
<body>
<main class="flyer">

  <!-- Header -->
  <div class="hero-photo" role="img" aria-label="Photograph of a city skyline with a concrete high-rise under construction beside a tower crane, under an overcast sky"></div>
  <div class="hero-building" role="img" aria-label="Concrete building frame under construction"></div>
  <svg class="hero-waves" width="800" height="160" viewBox="0 0 800 160" aria-hidden="true">
    <path d="M0 70 C 200 20, 330 60, 460 100 C 560 130, 680 120, 800 100 L800 160 L0 160 Z" fill="#e9eaea"/>
    <path d="M0 50 C 180 15, 300 40, 470 95" fill="none" stroke="var(--green)" stroke-width="13"/>
    <path d="M0 80 C 200 35, 330 75, 470 112 C 580 138, 690 128, 800 110" fill="none" stroke="var(--green)" stroke-width="12"/>
  </svg>
  <div class="brand">
    <span class="brand-mark"></span>
    <span class="brand-name">Meridale<br>Slab Works<br>LLC</span>
  </div>

  <!-- Who we are -->
  <h2 class="abs who-title">WHO WE ARE</h2>
  <div class="abs tab-rule who-rule"></div>
  <p class="abs who-text"><strong>Meridale Slab Works</strong> LLC is a trusted industry leader in<br><strong>Rebar Post-Tension</strong> Cable Placement, <strong>Post-Tension Cable Repair,</strong> Concrete Repair &amp; Parking Garage Restoration.</p>

  <!-- Services -->
  <div class="services-band"></div>
  <h2 class="tab" style="top:411px;width:210px;">OUR SERVICES</h2>
  <div class="tab-rule" style="left:222px;top:423px;width:530px;"></div>
  <div class="services">
    <div class="service" style="width:186px;">
      <svg width="36" height="40" viewBox="0 0 36 40"><path d="M24 3a8 8 0 0 0-7 11L4 27l5 5 13-13a8 8 0 0 0 11-7l-5 3-4-2-1-4z" fill="var(--green)"/><rect x="6" y="33" width="22" height="5" fill="var(--green)"/></svg>
      <span>Post-Tension Cable<br>Repair</span>
    </div>
    <div class="service" style="width:184px;">
      <svg width="44" height="34" viewBox="0 0 44 34"><g stroke="var(--green)" stroke-width="4" stroke-linecap="round"><path d="M4 26 L36 6"/><path d="M8 30 L40 10"/><path d="M3 20 L32 3"/></g><path d="M28 28 l8 4" stroke="#444" stroke-width="2"/></svg>
      <span><b style="font-weight:600">Rebar &amp; PT</b><br>Cable Placement</span>
    </div>
    <div class="service" style="width:176px;">
      <svg width="36" height="40" viewBox="0 0 36 40"><path d="M18 2 L33 8 V20 C33 30 26 36 18 38 C10 36 3 30 3 20 V8 Z" fill="var(--green)"/><rect x="11" y="13" width="14" height="14" fill="#e4e5e5"/><rect x="14" y="16" width="8" height="11" fill="var(--green)"/></svg>
      <span>Concrete Repair<br>&amp; Restoration</span>
    </div>
    <div class="service" style="width:170px;">
      <svg width="40" height="30" viewBox="0 0 40 30"><path d="M8 4 H32 L37 13 V26 H3 V13 Z" fill="#26302d"/><rect x="10" y="7" width="20" height="7" fill="#e4e5e5"/><circle cx="10" cy="19" r="2.5" fill="#e4e5e5"/><circle cx="30" cy="19" r="2.5" fill="#e4e5e5"/></svg>
      <span>Parking Garage<br>Restoration</span>
    </div>
  </div>

  <!-- Post-tension repair panel -->
  <section class="panel">
    <h2 class="panel-title">POST-TENSION REPAIR &amp; CONCRETE RESTORATION</h2>
    <p class="panel-tagline">Ensuring the strength and longevity of your concrete structures.</p>
    <div class="benefits">
      <div class="benefit" style="width:213px;"><h3>Structural Safety</h3><p style="text-align:left;padding-left:35px;">Damaged cables compromise stability.</p></div>
      <div class="benefit" style="width:250px;"><h3>Extended Building Life</h3><p>Proper repairs extend lifespan.</p></div>
      <div class="benefit" style="width:255px;"><h3>Cost-Effective Protection</h3><p>Prevent costly future damage.</p></div>
    </div>
  </section>

  <!-- Warning signs -->
  <h2 class="tab" style="top:711px;width:368px;">WARNING SIGNS OF CABLE ISSUES</h2>
  <div class="tab-rule" style="left:375px;top:723px;width:378px;"></div>
  <div class="signs">
    <div class="sign" style="width:166px;">
      <div class="sign-photo" role="img" aria-label="Photograph of cracked concrete surface" style="background:linear-gradient(135deg,#8d9190,#6e7271);"></div>
      <div class="sign-label"><svg width="18" height="16" viewBox="0 0 18 16"><path d="M9 1 L17 15 H1 Z" fill="var(--green-dark)"/><rect x="8.2" y="6" width="1.6" height="5" fill="#fff"/><rect x="8.2" y="12" width="1.6" height="1.6" fill="#fff"/></svg>Cracked Concrete</div>
    </div>
    <div class="sign" style="width:181px;">
      <div class="sign-photo" role="img" aria-label="Photograph of a corrugated post-tension cable with a copper anchor" style="background:linear-gradient(135deg,#5d6160,#8c8d8a 60,#b07b52);"></div>
      <div class="sign-label"><svg width="20" height="16" viewBox="0 0 20 16"><circle cx="5" cy="11" r="3.5" fill="var(--green-dark)"/><circle cx="12" cy="5" r="3" fill="var(--green-dark)"/><circle cx="15" cy="12" r="2.5" fill="var(--green-dark)"/></svg>Popping Sounds</div>
    </div>
    <div class="sign" style="width:165px;">
      <div class="sign-photo" role="img" aria-label="Photograph of exposed post-tension cables on a slab" style="background:linear-gradient(135deg,#4f5453,#8a8e8d);"></div>
      <div class="sign-label"><svg width="14" height="18" viewBox="0 0 14 18"><path d="M7 1 C 10 6, 13 9, 13 12 A6 6 0 0 1 1 12 C 1 9, 4 6, 7 1 Z" fill="var(--green-dark)"/></svg>Exposed Cables</div>
    </div>
    <div class="sign" style="width:182px;">
      <div class="sign-photo" role="img" aria-label="Photograph of water leaking onto broken concrete" style="background:linear-gradient(135deg,#6c6e6c,#9aa4a8 55%,#4c5658);"></div>
      <div class="sign-label"><svg width="14" height="18" viewBox="0 0 14 18"><path d="M7 1 C 10 6, 13 9, 13 12 A6 6 0 0 1 1 12 C 1 9, 4 6, 7 1 Z" fill="var(--green-dark)"/></svg>Water Leaks</div>
    </div>
  </div>

  <!-- Repair process -->
  <h2 class="tab" style="top:859px;width:265px;">OUR REPAIR PROCESS</h2>
  <div class="tab-rule" style="left:272px;top:871px;width:481px;"></div>
  <div class="process">
    <div class="step" style="left:0;top:0;width:228px;">
      <svg width="26" height="30" viewBox="0 0 26 30"><path d="M13 1 L25 6 V15 C25 23 19 27 13 29 C7 27 1 23 1 15 V6 Z" fill="var(--green)"/><circle cx="12" cy="14" r="5" fill="none" stroke="#fff" stroke-width="2"/><path d="M15.5 17.5 L19 21" stroke="#fff" stroke-width="2"/></svg>Inspection &amp; Assessment</div>
    <div class="step" style="left:0;top:36px;width:228px;">
      <svg width="26" height="30" viewBox="0 0 26 30"><path d="M13 1 L25 6 V15 C25 23 19 27 13 29 C7 27 1 23 1 15 V6 Z" fill="var(--green)"/><path d="M7 15 L11 19 L19 11" fill="none" stroke="#fff" stroke-width="2.5"/></svg>Advanced Repair Technology</div>
    <div class="col-rule" style="left:244px;top:0;height:68px;"></div>
    <div class="step" style="left:256px;top:0;width:190px;">
      <svg width="30" height="30" viewBox="0 0 30 30"><path d="M13 1 L25 6 V15 C25 23 19 27 13 29 C7 27 1 23 1 15 V6 Z" fill="var(--green)"/><path d="M5 20 L28 8" stroke="#555" stroke-width="2.5"/></svg>Advanced Repair Technology</div>
    <div class="step" style="left:256px;top:36px;width:190px;">
      <svg width="30" height="30" viewBox="0 0 30 30"><path d="M13 1 L25 6 V15 C25 23 19 27 13 29 C7 27 1 23 1 15 V6 Z" fill="var(--green)"/><path d="M5 16 L10 12 L15 15 L21 12" fill="none" stroke="#fff" stroke-width="2"/></svg>Client-Focused Solutions</div>
    <div class="col-rule" style="left:460px;top:0;height:68px;"></div>
    <div class="step" style="left:470px;top:0;width:236px;">
      <svg width="26" height="30" viewBox="0 0 26 30"><path d="M13 1 L25 6 V15 C25 23 19 27 13 29 C7 27 1 23 1 15 V6 Z" fill="var(--green)"/><circle cx="13" cy="15" r="7" fill="#fff"/><path d="M9.5 15 L12 17.5 L16.5 12.5" fill="none" stroke="var(--green)" stroke-width="2"/></svg>Sealing &amp; Protection</div>
  </div>

  <!-- Why choose us -->
  <h2 class="tab" style="top:980px;width:230px;">WHY CHOOSE US</h2>
  <div class="tab-rule" style="left:234px;top:992px;width:150px;"></div>
  <ul class="why">
    <li><span class="tick-box"><svg width="12" height="10" viewBox="0 0 12 10"><path d="M1 5 L4.5 8.5 L11 1.5" fill="none" stroke="#fff" stroke-width="2"/></svg></span>Experienced &amp; Skilled Team</li>
    <li><span class="tick-box"><svg width="12" height="10" viewBox="0 0 12 10"><path d="M1 5 L4.5 8.5 L11 1.5" fill="none" stroke="#fff" stroke-width="2"/></svg></span>Advanced Repair Technology</li>
    <li><span class="tick-box"><svg width="12" height="10" viewBox="0 0 12 10"><path d="M1 5 L4.5 8.5 L11 1.5" fill="none" stroke="#fff" stroke-width="2"/></svg></span>Client-Focused Solutions</li>
  </ul>

  <div class="footer-band"></div>
  <p class="abs updated">Updated, January 13, 2026</p>

  <!-- Contact -->
  <section class="contact">
    <h2>CONTACT US</h2>
    <div class="contact-head-rule"></div>
    <div class="contact-line contact-phone">
      <svg width="24" height="24" viewBox="0 0 24 24"><path d="M6 2 L10 6 L8 9 C9 12 12 15 15 16 L18 14 L22 18 L19 22 C11 21 3 13 2 5 Z" fill="none" stroke="#fff" stroke-width="1.8"/><path d="M14 3 A7 7 0 0 1 21 10 M14 7 A3 3 0 0 1 17 10" fill="none" stroke="#fff" stroke-width="1.6"/></svg>123-456-7890</div>
    <div class="contact-line contact-email">
      <svg width="24" height="16" viewBox="0 0 24 16"><rect x="1" y="1" width="22" height="14" fill="none" stroke="#fff" stroke-width="1.6"/><path d="M1 1 L12 9 L23 1" fill="none" stroke="#fff" stroke-width="1.6"/></svg>info@meridaleslabworks.com</div>
    <div class="contact-line contact-web">
      <svg width="22" height="22" viewBox="0 0 22 22"><g fill="none" stroke="#fff" stroke-width="1.5"><circle cx="11" cy="11" r="9.5"/><ellipse cx="11" cy="11" rx="4" ry="9.5"/><path d="M1.5 11 H20.5 M3 6 H19 M3 16 H19"/></g></svg>www.meridaleslabworks.com</div>
  </section>

</main>
</body>
</html>
```